Ward Compass Business Card Design*

We need a business card design for our company Ward Compass. Our company is specialized in providing online consulting services regarding medical institutions, hospitals and doctors. We work with patients worldwide looking to choose between healthcare providers. We have a website you may use as a reference, where we list doctors and clinics worldwide. So we target Medical providers as well as patients worldwide.
Target Market(s)
Medical Providers and patients around the world
Industry/Entity Type
Medical
Contact Information for Business Card
Salwa Kettani
CEO
+90 612 348 2175
info@wardcompass.example
www.wardcompass.example
14 Annakhil 7 H.R.B. Rabat, Morocco
Requirements
Must have
- Company logo/name on one full side, personal info and smaller logo and company name on the other side.
Nice to have
- Smart and elegant design

```html
<!DOCTYPE html>
<html lang="en">
<head>
<meta charset="utf-8">
<title>Ward Compass – Business Card</title>
<link rel="stylesheet" href="https://fonts.googleapis.com/css2?family=Montserrat:wght@400;600;700&display=swap">
<style>
  :root {
    --navy: #0e2e63;
    --royal: #163a8a;
    --slate: #5c6470;
    --ink: #1f2a44;
    --paper: #f4f5f7;
    --backdrop: #2b2b2d;
    --rule: #c3c7cf;
  }
  * { box-sizing: border-box; margin: 0; padding: 0; }
  html, body { width: 1200px; height: 997px; overflow: hidden; }
  body {
    background: var(--backdrop);
    font-family: "Montserrat", Arial, sans-serif;
    position: relative;
  }
  .card {
    position: absolute;
    width: 600px;
    height: 343px;
    border-radius: 18px;
    overflow: hidden;
    box-shadow: 0 18px 40px rgba(0,0,0,.45);
  }
  /* Front side */
  .card--front {
    left: 300px; top: 90px;
    background: var(--royal);
  }
  .card--front .brand {
    position: absolute;
    left: 70px; top: 120px;
    display: flex; align-items: center; gap: 18px;
    color: #ffffff;
  }
  .brand__dot {
    width: 58px; height: 58px;
    border-radius: 50%;
    border: 7px solid currentColor;
  }
  .brand__name {
    font-weight: 600;
    font-size: 36px;
    letter-spacing: 3px;
    text-transform: uppercase;
  }
  .card--front .strip {
    position: absolute;
    left: 0; right: 0; bottom: 0;
    height: 62px;
    background: var(--paper);
    display: flex; align-items: center; justify-content: center;
    color: var(--navy);
    font-weight: 600;
    font-size: 16px;
    letter-spacing: 3px;
  }
  /* Back side */
  .card--back {
    left: 300px; top: 510px;
    background: linear-gradient(135deg, #ffffff 0%, #e9ebee 100%);
  }
  .card--back .brand {
    position: absolute;
    left: 60px; top: 50px;
    display: flex; align-items: center; gap: 14px;
    color: var(--navy);
  }
  .card--back .brand__dot { width: 44px; height: 44px; border-width: 6px; }
  .card--back .brand__name { font-size: 28px; letter-spacing: 2px; }
  .holder {
    position: absolute;
    left: 60px; top: 168px;
    color: var(--navy);
  }
  .holder__name { font-weight: 700; font-size: 19px; letter-spacing: .5px; text-transform: uppercase; }
  .holder__role { font-weight: 600; font-size: 13px; color: var(--ink); margin-top: 2px; }
  .divider {
    position: absolute;
    left: 300px; top: 138px;
    width: 2px; height: 80px;
    background: linear-gradient(var(--rule), var(--navy), var(--rule));
  }
  .contacts {
    position: absolute;
    left: 325px; top: 142px;
    list-style: none;
    color: var(--slate);
    font-size: 14px;
  }
  .contacts li { display: flex; align-items: center; gap: 10px; height: 24px; }
  .contacts svg { width: 14px; height: 14px; fill: var(--navy); }
  .card--back .band {
    position: absolute;
    left: 0; right: 0; bottom: 0;
    height: 78px;
    background: var(--navy);
    display: flex; align-items: center; justify-content: center;
    color: #e6e9f0;
    font-size: 16px;
    letter-spacing: .5px;
  }
</style>
</head>
<body>
  <section class="card card--front" aria-label="Card front">
    <div class="brand">
      <span class="brand__dot"></span>
      <span class="brand__name">Ward Compass</span>
    </div>
    <div class="strip">www.wardcompass.example</div>
  </section>

  <section class="card card--back" aria-label="Card back">
    <div class="brand">
      <span class="brand__dot"></span>
      <span class="brand__name">Ward Compass</span>
    </div>
    <div class="holder">
      <p class="holder__name">Salwa Kettani</p>
      <p class="holder__role">CEO</p>
    </div>
    <div class="divider"></div>
    <ul class="contacts">
      <li>
        <svg viewBox="0 0 16 16" aria-hidden="true"><path d="M3 1h3l1.5 4-2 1.5a9 9 0 0 0 4 4L11 8.5l4 1.5v3a2 2 0 0 1-2 2A13 13 0 0 1 1 3a2 2 0 0 1 2-2z"/></svg>
        +90 612 348 2175
      </li>
      <li>
        <svg viewBox="0 0 16 16" aria-hidden="true"><path d="M1 3h14v10H1z M2 4l6 5 6-5" fill="none" stroke="#0e2e63" stroke-width="1.6"/></svg>
        info@wardcompass.example
      </li>
      <li>
        <svg viewBox="0 0 16 16" aria-hidden="true"><circle cx="8" cy="8" r="6.5" fill="none" stroke="#0e2e63" stroke-width="1.5"/><path d="M1.5 8h13M8 1.5c-3 3.5-3 9.5 0 13M8 1.5c3 3.5 3 9.5 0 13" fill="none" stroke="#0e2e63" stroke-width="1.2"/></svg>
        www.wardcompass.example
      </li>
    </ul>
    <div class="band">14 Annakhil 7 H.R.B. Rabat, Morocco</div>
  </section>
</body>
</html>
```